Lanternfield Drinks business cards

We need a business card design for our new logo. The company is modern, progressive, professional, yet approachable. The key products are ready to drink bottles and cans of coffee based beverages.
These cards will be a critical part of the first impression made by our sales organization, business development team, and all external facing personnel.
Card can be a vertical or horizontal orientation.

Target Market(s)

Customers, suppliers, business partners

Industry/Entity Type

Business

Contact Information for Business Card

Business cards should feature Company Name and Logo.

Font styles to use
Serif

Colors

Designer to choose colors to be used in the design.

Requirements
Must have
• Strong readability of Name, phone #, mobile number and email address.
• Job title, website url, Street Address, and other details can be secondary level readability.
Nice to have
• High impact, simplistic quality design.
• Ok to utilize the 'H in the box' separate from the company name

```html
<!DOCTYPE html>
<html lang="en">
<head>
<meta charset="utf-8">
<title>Lanternfield Drinks — Business Cards</title>
<link href="https://fonts.googleapis.com/css2?family=Crimson+Text:ital,wght@0,400;0,600;0,700;1,400&display=swap" rel="stylesheet">
<style>
  :root {
    --backdrop: #3b3b3c;
    --card: #1e1e1f;
    --card-edge: #2a2a2b;
    --emboss: #5a5a5c;
    --accent: #e2572a;
    --accent-soft: #f08a2c;
    --ink: #f4f1ec;
  }
  * { margin: 0; padding: 0; box-sizing: border-box; }
  html, body { width: 799px; height: 1200px; overflow: hidden; }
  body {
    background: radial-gradient(ellipse at 50% 40%, #4a4a4b 0%, var(--backdrop) 70%);
    font-family: "Crimson Text", Georgia, serif;
    position: relative;
  }
  .card {
    position: absolute;
    left: 80px;
    width: 640px;
    height: 366px;
    background: var(--card);
    border: 1px solid var(--card-edge);
    border-radius: 4px;
    box-shadow: 0 18px 40px rgba(0,0,0,0.5);
  }
  .card--front { top: 120px; }
  .card--back { top: 714px; }

  /* front */
  .front-mark {
    position: absolute; inset: 0;
    display: flex; align-items: center; justify-content: center; gap: 22px;
  }
  .front-square {
    width: 110px; height: 110px;
    border: 10px solid var(--emboss);
  }
  .front-name {
    color: var(--emboss);
    font-size: 40px; font-weight: 600;
    letter-spacing: 1px; text-transform: uppercase; line-height: 1.05;
  }

  /* back */
  .brand {
    position: absolute; left: 56px; top: 46px;
    display: flex; align-items: center; gap: 18px;
  }
  .brand-square {
    width: 74px; height: 74px;
    border: 6px solid var(--accent);
  }
  .brand-name {
    color: var(--accent);
    font-size: 42px; font-weight: 700;
    text-transform: uppercase; letter-spacing: 1px; line-height: 1;
  }
  .divider {
    position: absolute; left: 300px; top: 176px;
    width: 2px; height: 132px;
    background: var(--accent-soft);
  }
  .person {
    position: absolute; right: 360px; top: 172px;
    text-align: right; color: var(--ink);
    font-size: 19px; line-height: 1.3;
  }
  .person-name { color: var(--accent); font-size: 25px; font-weight: 700; line-height: 1.2; }
  .person-title { font-style: italic; font-size: 17px; }
  .contacts {
    position: absolute; left: 322px; top: 186px;
    list-style: none; color: var(--ink);
    font-size: 20px; line-height: 28px;
  }
  .contacts li { display: flex; align-items: center; gap: 12px; }
  .contacts svg { width: 16px; height: 16px; fill: var(--accent); flex: none; }
</style>
</head>
<body>
  <section class="card card--front" aria-label="Card front">
    <div class="front-mark">
      <div class="front-square"></div>
      <div class="front-name">Lanternfield<br>Drinks</div>
    </div>
  </section>

  <section class="card card--back" aria-label="Card back">
    <div class="brand">
      <div class="brand-square"></div>
      <div class="brand-name">Lanternfield Drinks</div>
    </div>

    <div class="person">
      <p class="person-name">Mara Ellison Vale</p>
      <p class="person-title">Managing Director</p>
      <p>48 Harbor Row,</p>
      <p>Millbrook, US 10234</p>
    </div>

    <div class="divider"></div>

    <ul class="contacts">
      <li>
        <svg viewBox="0 0 16 16" aria-hidden="true"><path d="M3 1h3l1 4-2 1a9 9 0 0 0 5 5l1-2 4 1v3a2 2 0 0 1-2 2A13 13 0 0 1 1 3a2 2 0 0 1 2-2z"/></svg>
        555.210.4836
      </li>
      <li>
        <svg viewBox="0 0 16 16" aria-hidden="true"><path d="M4 0h8a1 1 0 0 1 1 1v14a1 1 0 0 1-1 1H4a1 1 0 0 1-1-1V1a1 1 0 0 1 1-1zm1 2v10h6V2zm3 11a1 1 0 1 0 0 2 1 1 0 0 0 0-2z"/></svg>
        555.318.9027
      </li>
      <li>
        <svg viewBox="0 0 16 16" aria-hidden="true"><path d="M1 3h14v10H1zm1.5 1.2L8 8.5l5.5-4.3z"/></svg>
        mara@lanternfield.com
      </li>
      <li>
        <svg viewBox="0 0 16 16" aria-hidden="true"><path d="M8 1a7 7 0 1 0 0 14A7 7 0 0 0 8 1zm0 1.5c.9 1 1.5 2.6 1.7 4.5H6.3C6.5 5.1 7.1 3.5 8 2.5zM2.6 7h2.2c.1-1.6.5-3 1.1-4A5.6 5.6 0 0 0 2.6 7zm0 2a5.6 5.6 0 0 0 3.3 4c-.6-1-1-2.4-1.1-4zm3.7 0h3.4c-.2 1.9-.8 3.5-1.7 4.5-.9-1-1.5-2.6-1.7-4.5zm4.9 0c-.1 1.6-.5 3-1.1 4a5.6 5.6 0 0 0 3.3-4zm2.2-2a5.6 5.6 0 0 0-3.3-4c.6 1 1 2.4 1.1 4z"/></svg>
        www.lanternfield.com
      </li>
    </ul>
  </section>
</body>
</html>
```